Fenwick Grading LTD - website for irrigation & Landscape Lighting & Buried service wire

Looking for a website to help promote my business with Irrigation (installation, service, etc) and buried service wire/drainage solutions.

Commercial/Residential

Landscape lighting.

I’ll get photos in the trucks and trailers to upload as well maybe the machine as well.

Target Market(s)

Homeowners who want green grass and beautiful gardens. Beautiful landscape lighting

Industry/Entity Type

Irrigation systems and landscape lighting and buried service wire to homes and offering Drainage soltions.

Coding

Coded - Design and coding required

Number of Pages Required

4 page

Colors
F0912C
F2A743
F7CA91
FBE8D2
FDF5EE

Requirements
Must have
• was hoping to link up my email on fenwickgrading@mailbox-example.net with the website if possible.
Nice to have
• Page for Irrigation, page for landscape lighting, page buried service wire & drainage soltions.

```html
<!DOCTYPE html>
<html lang="en">
<head>
<meta charset="utf-8">
<title>Fenwick Grading LTD – Irrigation, Landscape Lighting &amp; Fiber Optic Installation</title>
<link rel="stylesheet" href="https://fonts.googleapis.com/css2?family=Montserrat:wght@400;500;600;700&family=Oswald:wght@500&display=swap">
<style>
:root{
  --orange:#F0912C;
  --orange-2:#F2A743;
  --peach-3:#F7CA91;
  --peach:#FBE8D2;
  --cream:#FDF5EE;
  --ink:#1e1e1e;
  --text:#5a5a5a;
  --white:#ffffff;
  --footer:#262826;
}
*{box-sizing:border-box;margin:0;padding:0}
html,body{width:1200px;height:4474px;overflow:hidden}
body{position:relative;font-family:"Montserrat",sans-serif;color:var(--ink);background:var(--white)}
.abs{position:absolute}
a{color:inherit;text-decoration:none}

/* hero */
.hero{position:absolute;left:0;top:0;width:1200px;height:620px;overflow:hidden}
.hero-photo{position:absolute;inset:0;background:
  radial-gradient(circle at 18% 12%,rgba(255,200,120,.35),transparent 22%),
  radial-gradient(ellipse at 75% 45%,#3f5a2a 0%,transparent 55%),
  linear-gradient(180deg,#2c3a22 0%,#3c5226 40%,#4e6b2c 70%,#2f3f1f 100%)}
.hero-shade{position:absolute;inset:0;background:linear-gradient(90deg,rgba(0,0,0,.45),rgba(0,0,0,.15) 60%,rgba(0,0,0,.25))}
.hero-curve{position:absolute;left:0;top:0}
.brand{position:absolute;left:141px;top:28px;color:var(--orange);font-weight:700;font-size:26px;line-height:1}
.brand small{display:block;font-size:13px;font-weight:600;color:var(--white);letter-spacing:1.5px;margin-top:6px}
.nav{position:absolute;top:28px;left:509px;display:flex;align-items:center;height:35px;gap:29px;font-size:12px;font-weight:500;color:var(--white)}
.nav .nav-cta{background:var(--orange);padding:0 19px;height:35px;line-height:35px;margin-left:1px}
.hero-title{position:absolute;left:141px;top:180px;width:480px;font-family:"Oswald",sans-serif;font-weight:500;font-size:35px;line-height:49px;color:var(--white)}
.hero-text{position:absolute;left:141px;top:337px;width:450px;font-size:12px;line-height:22px;color:var(--white)}
.btn{display:inline-block;background:var(--orange);color:var(--white);font-size:11px;font-weight:600}
.hero-btn{position:absolute;left:141px;top:417px;width:104px;height:36px;line-height:36px;text-align:center}
.hero-mark{position:absolute;left:700px;top:300px;font-size:30px;font-weight:700;color:rgba(255,255,255,.18);letter-spacing:2px}

/* headings */
.h2{font-size:25px;font-weight:600;color:var(--ink)}
.h2 span{color:var(--orange)}
.eyebrow{font-size:10px;font-weight:700;letter-spacing:2px;color:var(--orange);text-transform:uppercase}

/* benefits */
.benefits-title{position:absolute;left:0;width:1200px;top:668px;text-align:center}
.card{position:absolute;top:740px;width:291px;height:238px;background:var(--white);border-radius:8px;box-shadow:0 4px 22px rgba(0,0,0,.09);text-align:center}
.card-icon{width:71px;height:71px;margin:21px auto 0;border-radius:12px;background:var(--orange);display:flex;align-items:center;justify-content:center}
.card h3{font-size:15px;font-weight:600;margin-top:22px}
.card p{font-size:11px;line-height:20px;color:var(--text);margin:12px 28px 0}
.card .more{display:inline-block;margin-top:12px;font-size:12px;font-weight:500;color:var(--orange);text-decoration:underline}

/* about */
.photo{position:absolute}
.frame{position:absolute;background:var(--white);border-radius:10px;box-shadow:0 4px 16px rgba(0,0,0,.12);padding:6px}
.frame .fill{width:100%;height:100%;border-radius:6px}
.about-text{position:absolute;left:639px;top:1080px;width:420px}
.about-text .h2{margin-top:14px}
.body-p{font-size:12.5px;line-height:22.5px;color:var(--text)}
.about-text .body-p{margin-top:18px}
.pill{display:inline-block;background:var(--orange);color:var(--white);font-size:11px;font-weight:600;letter-spacing:.5px;border-radius:18px;text-align:center}
.about-actions{position:absolute;left:639px;top:1393px;display:flex;align-items:center}
.about-actions .pill{width:122px;height:33px;line-height:33px}
.phone-ring{width:33px;height:33px;border-radius:50%;border:2px solid var(--orange);margin-left:19px;display:flex;align-items:center;justify-content:center}
.about-actions .num{font-size:13px;font-weight:600;margin-left:12px}

/* services */
.band{position:absolute;left:0;width:1200px}
.service{position:absolute;width:420px}
.service .h2{margin-top:12px}
.sub{margin-top:18px;border-left:2px solid var(--orange);padding-left:11px;font-size:12px;font-weight:500;line-height:22px;color:var(--ink)}
.service .body-p{margin-top:14px}
.service .pill{margin-top:26px;width:122px;height:33px;line-height:33px}
.blob{position:absolute}
.name-ghost{position:absolute;font-size:22px;font-weight:700;color:rgba(240,145,44,.14)}

/* testimonial */
.center-block{position:absolute;left:0;width:1200px;text-align:center}
.quote{position:absolute;left:225px;width:750px;top:3275px;text-align:center;font-size:12.5px;line-height:22.5px;color:var(--ink)}
.avatar{position:absolute;left:512px;top:3380px;width:61px;height:61px;border-radius:50%;background:linear-gradient(160deg,#c9ccd0,#6f7479)}
.person{position:absolute;left:593px;top:3392px}
.person b{display:block;font-size:14px;font-weight:600;color:var(--orange)}
.person span{display:block;font-size:12px;color:var(--text);margin-top:6px}

/* contact */
.contact{position:absolute;left:141px;top:3526px;width:917px;height:547px;background:var(--peach);border-radius:20px}
.field{position:absolute;background:var(--white);border-radius:4px;font-size:11px;color:#8a8a8a;padding:14px 21px}
.submit{position:absolute;left:397px;top:480px;width:124px;height:34px;line-height:34px;text-align:center}

/* footer */
.footer{position:absolute;left:0;top:4160px;width:1200px;height:314px;background:linear-gradient(180deg,#2d302c,#1f211f)}
.footer .brand{top:72px;font-size:30px}
.footer .brand small{font-size:15px}
.fcol{position:absolute;top:68px;color:var(--white);font-size:12px}
.fcol h4{font-size:15px;font-weight:500;color:var(--orange);margin-bottom:16px}
.fcol li{list-style:none;line-height:28px}
.info{display:flex;gap:10px;line-height:20px;margin-bottom:10px}
.rule{position:absolute;left:141px;top:248px;width:917px;height:1px;background:rgba(255,255,255,.25)}
.copy{position:absolute;left:141px;top:278px;font-size:12px;color:var(--white)}
.socials{position:absolute;left:926px;top:274px;display:flex;gap:8px}
.socials i{display:block;width:28px;height:28px;border-radius:50%;background:var(--orange)}
</style>
</head>
<body>

<!-- hero -->
<header class="hero">
  <div class="hero-photo" role="img" aria-label="Evening garden with lawn, shrubs and lit bollard lights"></div>
  <div class="hero-shade"></div>
  <div class="hero-mark">Fenwick Grading LTD</div>
  <svg class="hero-curve" width="1200" height="620" viewBox="0 0 1200 620">
    <path d="M0 542 Q600 690 1200 542 V620 H0Z" fill="#fff"/>
    <path d="M0 542 Q600 690 1200 542" fill="none" stroke="#F0912C" stroke-width="3"/>
  </svg>
  <div class="brand">Fenwick<small>GRADING LTD</small></div>
  <nav class="nav">
    <a href="#">Home</a><a href="#">Irrigation</a><a href="#">Landscape Lighting</a><a href="#">Fiber Optic Installation</a>
    <a class="nav-cta" href="#">Contact Us</a>
  </nav>
  <h1 class="hero-title">Transform Your Outdoor Space With Our Expert Irrigation And Lighting Solutions</h1>
  <p class="hero-text">Get the perfect blend of form and function with our state-of-the-art irrigation systems and landscape lighting.Trust our experienced team to deliver top-notch fiber optic installation for your home</p>
  <a class="btn hero-btn" href="#">Contact Us</a>
</header>

<!-- benefits -->
<h2 class="h2 benefits-title">Benefits Of Our <span>Services</span></h2>
<div class="card" style="left:141px">
  <div class="card-icon"><svg width="38" height="38" viewBox="0 0 38 38" fill="none" stroke="#fff" stroke-width="2"><path d="M19 5C14 12 11 16 11 20a8 8 0 0 0 16 0c0-4-3-8-8-15z"/><path d="M5 30c5 3 9 3 14 0s9-3 14 0"/></svg></div>
  <h3>Saving Water</h3>
  <p>Lorem Ipsum is simply dummy text of the printing and typesetting industry.</p>
  <a class="more" href="#">Read More &nbsp;→</a>
</div>
<div class="card" style="left:455px">
  <div class="card-icon"><svg width="38" height="38" viewBox="0 0 38 38" fill="none" stroke="#fff" stroke-width="2"><path d="M6 18L19 7l13 11"/><path d="M10 15v16h18V15"/><path d="M16 31v-8h6v8"/></svg></div>
  <h3>Enhancing Curb Appeal</h3>
  <p>Lorem Ipsum is simply dummy text of the printing and typesetting industry.</p>
  <a class="more" href="#">Read More &nbsp;→</a>
</div>
<div class="card" style="left:768px">
  <div class="card-icon"><svg width="38" height="38" viewBox="0 0 38 38" fill="none" stroke="#fff" stroke-width="2"><path d="M19 5l11 4v9c0 8-5 12-11 15C13 30 8 26 8 18V9z"/><path d="M14 19l4 4 7-8"/></svg></div>
  <h3>Improving Safety And Security</h3>
  <p>Lorem Ipsum is simply dummy text of the printing and typesetting industry.</p>
  <a class="more" href="#">Read More &nbsp;→</a>
</div>

<!-- about -->
<div class="photo" style="left:243px;top:1072px;width:229px;height:369px;border-radius:0 115px 115px 115px;border:2px solid var(--orange);overflow:hidden">
  <div role="img" aria-label="Lawn sprinkler spraying water at sunset" style="width:100%;height:100%;background:linear-gradient(170deg,#6b5a35,#a37a3c 45%,#3d4a24)"></div>
</div>
<div class="frame" style="left:210px;top:1063px;width:82px;height:92px"><div class="fill" role="img" aria-label="Rows of green plants" style="background:linear-gradient(160deg,#9cbf62,#4d7a2c)"></div></div>
<div class="frame" style="left:141px;top:1273px;width:133px;height:151px"><div class="fill" role="img" aria-label="Sprinkler watering a lawn" style="background:linear-gradient(160deg,#c6c27a,#5d7a30)"></div></div>
<div class="frame" style="left:455px;top:1282px;width:122px;height:113px;display:flex;align-items:center;justify-content:center;font-size:13px;font-weight:700;color:var(--orange);text-align:center">Fenwick<br>Grading</div>
<div class="about-text">
  <div class="eyebrow">Fenwick Grading</div>
  <h2 class="h2"><span>About</span> Fenwick Grading</h2>
  <p class="body-p">Welcome to our professional irrigation systems and landscape lighting services. We specialize in providing homeowners with lush green lawns, vibrant gardens, and captivating outdoor lighting.</p>
  <p class="body-p">With our expertise in irrigation installation, service, landscape lighting, and fiber optic installation, we can transform your home into a stunning oasis. Discover the possibilities and enhance the beauty of your outdoor spaces with our top-notch services.</p>
</div>
<div class="about-actions">
  <a class="pill" href="#">LEARN MORE</a>
  <div class="phone-ring"><svg width="15" height="15" viewBox="0 0 24 24" fill="#F0912C"><path d="M6.6 10.8a15 15 0 0 0 6.6 6.6l2.2-2.2a1 1 0 0 1 1-.25 11.4 11.4 0 0 0 3.6.6 1 1 0 0 1 1 1V20a1 1 0 0 1-1 1A17 17 0 0 1 3 4a1 1 0 0 1 1-1h3.5a1 1 0 0 1 1 1c0 1.25.2 2.45.6 3.6a1 1 0 0 1-.25 1z"/></svg></div>
  <span class="num">123-456-7890</span>
</div>

<!-- irrigation -->
<svg class="band" style="top:1511px" width="1200" height="521" viewBox="0 0 1200 521"><path d="M0 0C250 40 600 50 900 18 1030 5 1130 0 1200 8V490C950 530 650 470 380 500 200 518 80 512 0 498Z" fill="#FBE8D2"/></svg>
<div class="service" style="left:141px;top:1600px">
  <div class="eyebrow">Fenwick Grading</div>
  <h2 class="h2">Irrigation <span>Systems</span></h2>
  <div class="sub">Efficient and Effective Watering Solutions for Your Lawn and Garden</div>
  <p class="body-p">Our irrigation systems are designed to provide your lawn and garden with the right amount of water, without wasting a single drop. With our expert installation and service, you can rest assured that your plants will receive the nourishment they need to thrive.</p>
  <a class="pill" href="#">LEARN MORE</a>
</div>
<svg class="blob" style="left:662px;top:1595px" width="395" height="375" viewBox="0 0 395 375" role="img" aria-label="Rotating sprinkler head spraying over a field">
  <defs><linearGradient id="g1" x1="0" y1="0" x2="0" y2="1"><stop offset="0" stop-color="#b9c4cc"/><stop offset=".6" stop-color="#7e8f6a"/><stop offset="1" stop-color="#3e5a2a"/></linearGradient></defs>
  <path d="M18 330C-5 250 15 120 90 55 160-5 260 0 330 60 390 115 380 190 330 250 275 320 170 370 80 365 45 362 28 350 18 330Z" fill="url(#g1)" transform="translate(8 4)"/>
  <path d="M30 335C10 250 30 115 110 50 185 -8 290 5 355 75 405 135 380 210 320 270 260 330 150 375 70 365" fill="none" stroke="#F0912C" stroke-width="2"/>
</svg>
<div class="name-ghost" style="left:1020px;top:1905px">Fenwick</div>

<!-- landscape lighting -->
<svg class="blob" style="left:150px;top:2118px" width="385" height="382" viewBox="0 0 385 382" role="img" aria-label="Garden at dusk with path light and ornamental grasses">
  <defs><linearGradient id="g2" x1="0" y1="0" x2="1" y2="1"><stop offset="0" stop-color="#3a4a2a"/><stop offset=".5" stop-color="#5f7a3a"/><stop offset="1" stop-color="#2a3320"/></linearGradient></defs>
  <path d="M20 260C0 180 40 70 120 25 190-10 260 10 300 70 340 130 330 230 280 300 230 365 130 385 70 350 45 335 28 300 20 260Z" fill="url(#g2)"/>
  <path d="M140 12C210-5 290 30 330 100 375 180 340 280 280 330 220 375 140 382 85 362" fill="none" stroke="#F0912C" stroke-width="2"/>
</svg>
<div class="service" style="left:627px;top:2128px">
  <div class="eyebrow">Fenwick Grading</div>
  <h2 class="h2">Landscape <span>Lighting</span></h2>
  <div class="sub">Enhance Your Outdoor Space with Beautiful and Functional Lighting Solutions</div>
  <p class="body-p">Our landscape lighting solutions are designed to enhance the beauty and functionality of your outdoor space. From subtle pathway lighting to dramatic spotlights, we'll work with you to create a lighting plan that meets your needs and complements your landscape.</p>
  <a class="pill" href="#">LEARN MORE</a>
</div>

<!-- fiber optic -->
<svg class="band" style="top:2579px" width="1200" height="513" viewBox="0 0 1200 513"><path d="M0 12C200-2 420 0 700 20 950 40 1100 35 1200 25V470C950 500 650 520 380 505 220 496 90 490 0 498Z" fill="#FBE8D2"/></svg>
<div class="service" style="left:141px;top:2678px">
  <div class="eyebrow">Fenwick Grading</div>
  <h2 class="h2">Fiber Optic <span>Installation</span></h2>
  <div class="sub">Expert Installation of Fiber Optic Networks for Your Home</div>
  <p class="body-p">Our team of experienced professionals will install your fiber optic network with precision and care. We'll work with you to ensure that your home is equipped with the latest technology, providing you with fast and reliable internet, TV, and voice services.</p>
  <a class="pill" href="#">LEARN MORE</a>
</div>
<div class="name-ghost" style="left:455px;top:2950px">Fenwick</div>
<svg class="blob" style="left:662px;top:2645px" width="395" height="382" viewBox="0 0 395 382" role="img" aria-label="Technician's hands working with cables and a test meter on a table">
  <defs><linearGradient id="g3" x1="0" y1="0" x2="1" y2="1"><stop offset="0" stop-color="#d9d6d2"/><stop offset=".5" stop-color="#8a5a3a"/><stop offset="1" stop-color="#3a2a22"/></linearGradient></defs>
  <path d="M10 260C-10 170 40 60 140 20 230-12 320 20 355 100 390 180 350 270 280 330 210 385 110 385 55 340 30 320 16 290 10 260Z" fill="url(#g3)" transform="translate(8 2)"/>
  <path d="M150 8C240-10 340 30 375 120 405 200 355 290 280 340 210 385 110 380 50 345" fill="none" stroke="#F0912C" stroke-width="2"/>
</svg>

<!-- testimonial -->
<div class="center-block" style="top:3185px"><div class="eyebrow">Fenwick Grading</div></div>
<h2 class="h2 center-block" style="top:3218px">What Our <span style="color:var(--orange)">Client</span> Say</h2>
<p class="quote">“ Dana Whitfield is a Strategist, Author and Disability &amp; STEM Advocate who has dedicated her life to serving others. Marcus Founded Brightmoor Labs in 2014, a leading digital strategy studio, as well as Clearpath Digital in 2019, a technology firm committed to bridging the accessibility gap in product development. ”</p>
<svg class="abs" style="left:278px;top:3404px" width="38" height="14" viewBox="0 0 38 14" fill="none" stroke="#333" stroke-width="1.5"><path d="M37 7H2M8 1L2 7l6 6"/></svg>
<div class="avatar" role="img" aria-label="Client portrait"></div>
<div class="person"><b>Marcus Ellery</b><span>Web Designer</span></div>
<svg class="abs" style="left:884px;top:3404px" width="38" height="14" viewBox="0 0 38 14" fill="none" stroke="#333" stroke-width="1.5"><path d="M1 7h35M30 1l6 6-6 6"/></svg>

<!-- contact -->
<section class="contact">
  <div class="eyebrow" style="position:absolute;left:0;width:917px;text-align:center;top:52px">Fenwick Grading</div>
  <h2 class="h2" style="position:absolute;left:0;width:917px;text-align:center;top:80px">Contact <span>Us</span></h2>
  <p style="position:absolute;left:0;width:917px;text-align:center;top:131px;font-size:12.5px;color:var(--text)">Complete the form below to schedule your meeting with Fenwick Grading</p>
  <div class="field" style="left:74px;top:192px;width:375px;height:42px">First name</div>
  <div class="field" style="left:467px;top:192px;width:375px;height:42px">Email</div>
  <div class="field" style="left:74px;top:253px;width:375px;height:42px">Phone</div>
  <div class="field" style="left:467px;top:253px;width:375px;height:42px">Question</div>
  <div class="field" style="left:74px;top:312px;width:768px;height:137px">Message</div>
  <a class="pill submit" href="#">SUBMIT NOW</a>
</section>

<!-- footer -->
<footer class="footer">
  <div class="brand">Fenwick<small>GRADING LTD</small></div>
  <div class="fcol" style="left:459px"><h4>Quick Links</h4><ul><li>Home</li><li>Irrigation</li><li>Landscape Lighting</li><li>Fiber Optic Installation</li></ul></div>
  <div class="fcol" style="left:670px"><h4>Useful Links</h4><ul><li>Contact</li><li>Privacy Policy</li><li>Terms of Service</li></ul></div>
  <div class="fcol" style="left:839px;width:240px"><h4>Contact Info</h4>
    <div class="info"><svg width="16" height="18" viewBox="0 0 24 24" fill="#F0912C"><path d="M12 2a7 7 0 0 0-7 7c0 5 7 13 7 13s7-8 7-13a7 7 0 0 0-7-7zm0 9.5A2.5 2.5 0 1 1 12 6.5a2.5 2.5 0 0 1 0 5z"/></svg><span>Address Line 1, Address<br>Line 2, Address Line 3.</span></div>
    <div class="info" style="font-size:11px"><svg width="16" height="16" viewBox="0 0 24 24" fill="#F0912C"><path d="M3 5h18v14H3z"/><path d="M3 5l9 7 9-7" stroke="#262826" stroke-width="2" fill="none"/></svg><span>fenwickgrading@mailbox-example.net</span></div>
    <div class="info"><svg width="16" height="16" viewBox="0 0 24 24" fill="#F0912C"><path d="M6.6 10.8a15 15 0 0 0 6.6 6.6l2.2-2.2a1 1 0 0 1 1-.25 11.4 11.4 0 0 0 3.6.6 1 1 0 0 1 1 1V20a1 1 0 0 1-1 1A17 17 0 0 1 3 4a1 1 0 0 1 1-1h3.5a1 1 0 0 1 1 1c0 1.25.2 2.45.6 3.6a1 1 0 0 1-.25 1z"/></svg><span>123-456-7890</span></div>
  </div>
  <div class="rule"></div>
  <p class="copy">© 2024 Fenwick Grading. All rights reserved.</p>
  <div class="socials" aria-label="Social links"><i></i><i></i><i></i><i></i></div>
</footer>

</body>
</html>
```